Website re-design for Brightmoor LLC website ( has existing website )

Looking to do a complete re-design of Brightmoorllc. The existing website is dated and built in wordpress. The new website will not be wordpress. The project folder includes an overview.txt file with details on the project. The file also contains a list of websites that he/she likes which I am sure is very helpful .
Number of Pages Required
1 page

```html
<!DOCTYPE html>
<html lang="en">
<head>
<meta charset="utf-8">
<title>Brightmoor LLC – Lake Weed Removal</title>
<link rel="stylesheet" href="https://fonts.googleapis.com/css2?family=Raleway:wght@400;500;600&family=Roboto:wght@400;500;700&display=swap">
<style>
:root{
  --blue:#1b5cb3;
  --blue-dark:#134a96;
  --red:#d21044;
  --ink:#222831;
  --text:#444b55;
  --pale:#eef4fc;
  --navy:#0b0e1a;
  --line:#e3e7ee;
  --white:#ffffff;
}
*{box-sizing:border-box;margin:0;padding:0}
html,body{width:1200px;height:4608px;overflow:hidden;background:var(--white)}
body{font-family:"Roboto",Arial,sans-serif;color:var(--text);position:relative}
.abs{position:absolute}
.page{position:relative;width:1200px;height:4608px;overflow:hidden}

/* header */
.topbar{top:0;left:0;width:1200px;height:80px;background:var(--white)}
.brand{display:flex;align-items:center;gap:10px}
.brand-dot{width:50px;height:50px;border-radius:50%;background:var(--blue)}
.brand-name{font-family:"Raleway",sans-serif;font-size:30px;font-weight:500;color:var(--blue)}
.contact-mini{display:flex;align-items:center;gap:12px;font-size:15px;color:var(--ink)}
.contact-mini small{display:block;font-size:11px;font-weight:700;color:var(--blue);margin-bottom:3px}
.social{display:flex;gap:12px}
.social span{width:38px;height:38px;border-radius:50%;background:var(--blue)}
.navbar{top:80px;left:0;width:1200px;height:50px;background:var(--blue)}
.nav{left:110px;top:0;height:50px;display:flex;align-items:center;gap:27px;font-size:14.5px;color:var(--white);text-transform:uppercase}
.nav-phone{left:918px;top:0;width:282px;height:50px;background:var(--red);display:flex;align-items:center;gap:14px;padding-left:6px;color:var(--white);font-size:17px;font-weight:500}
.nav-phone i{width:38px;height:38px;border-radius:50%;background:var(--white);display:flex;align-items:center;justify-content:center}

/* hero */
.hero{top:130px;left:0;width:1200px;height:710px;background:linear-gradient(180deg,#3a5fa6 0%,#4d72b3 30%,#2a3f6a 55%,#1d2b47 100%)}
.hero-title{top:245px;width:1200px;text-align:center;font-family:"Raleway",sans-serif;font-size:60px;color:var(--white);font-weight:400}
.hero-sub{top:340px;width:1200px;text-align:center;font-family:"Raleway",sans-serif;font-size:38px;color:var(--white)}
.btn{display:inline-flex;align-items:center;gap:12px;border-radius:24px;background:var(--red);color:var(--white);font-size:14px;font-weight:700;text-transform:uppercase;padding:0 6px 0 22px;height:42px}
.btn i{width:32px;height:32px;border-radius:50%;background:var(--white);display:flex;align-items:center;justify-content:center}
.dots{top:594px;left:561px;display:flex;gap:6px}
.dots span{width:14px;height:14px;border-radius:50%;border:2px solid var(--white)}
.dots span.on{background:var(--white)}

/* headings */
.sec-title{width:1200px;text-align:center;font-family:"Raleway",sans-serif;font-size:34px;color:var(--ink)}
.rule{width:48px;height:4px;left:576px;background:var(--blue);border-radius:2px}

/* services */
.card{width:300px;height:313px}
.card-photo{top:0;left:0;width:300px;height:215px}
.card-body{top:179px;left:16px;width:270px;height:134px;background:var(--white);box-shadow:0 4px 14px rgba(0,0,0,.12);display:flex}
.card-icon{width:72px;height:134px;background:#f2f3f5;display:flex;align-items:flex-start;justify-content:center;padding-top:24px}
.card-icon span{width:40px;height:30px;border-radius:4px;background:var(--blue)}
.card-text{padding:20px 10px 0 12px;font-size:12.5px;line-height:23px;color:var(--text)}
.card-text b{display:block;font-size:14px;color:var(--ink);line-height:18px;margin-bottom:6px}
.card-plus{top:169px;left:246px;width:26px;height:26px;background:var(--blue);color:var(--white);font-size:18px;display:flex;align-items:center;justify-content:center}
.arrow-btn{width:38px;height:38px;border-radius:50%;display:flex;align-items:center;justify-content:center}

/* about */
.about{top:1470px;left:0;width:1200px;height:708px;background:var(--pale)}
.p-center{font-size:15.5px;line-height:30px;text-align:justify}
.about-photo{top:1725px;left:130px;width:384px;height:384px;border-radius:50%;border:4px solid var(--blue);padding:8px;background:var(--white)}
.about-photo div{width:100%;height:100%;border-radius:50%;background:linear-gradient(180deg,#c9d3dc 0%,#8c9aa8 45%,#2b3138 70%,#596b7b 100%)}
.sub-title{font-family:"Raleway",sans-serif;font-size:26px;color:var(--ink);border-left:4px solid var(--blue);padding-left:14px;line-height:30px}
.about-text{font-size:15.5px;line-height:30px;text-align:justify}
.about-text b{color:var(--red);font-weight:500}

/* results */
.result{width:233px;height:298px;background:var(--white);box-shadow:0 3px 12px rgba(0,0,0,.12)}
.result-photo{top:0;left:0;width:233px;height:250px}
.result-label{top:265px;width:233px;text-align:center;font-size:16px;font-weight:700;color:var(--ink)}
.result-label.after{color:var(--red)}
.dotgrid{background-image:radial-gradient(#c8ccd4 1.2px,transparent 1.4px);background-size:8px 8px}

/* testimonials */
.testi{top:2725px;left:0;width:1200px;height:543px;background:linear-gradient(180deg,#1e60bb,#1854a8)}
.testi-title{font-family:"Raleway",sans-serif;font-size:34px;color:var(--white)}
.testi-text{font-size:15px;line-height:23px;color:var(--white);text-align:justify}
.circle-photo{border-radius:50%;border:4px solid var(--white)}

/* faq */
.faq-open{top:3430px;left:170px;width:860px;height:177px;background:var(--white);box-shadow:0 4px 18px rgba(0,0,0,.1);border-left:4px solid var(--blue)}
.faq-item{left:170px;width:860px;height:57px;background:var(--white);border:1px solid var(--line);display:flex;align-items:center;justify-content:space-between;padding:0 40px 0 30px;font-size:15px;color:var(--text)}
.faq-item i{font-style:normal;color:var(--blue);font-size:22px;font-weight:700}

/* footer */
.footer{top:4041px;left:0;width:1200px;height:567px;background:var(--navy)}
.foot-head{font-size:16px;font-weight:700;color:var(--white);text-transform:uppercase}
.foot-head:after{content:"";display:block;width:34px;height:3px;background:var(--blue);margin-top:10px}
.foot-links{list-style:none;font-size:15px;color:#e6e8ee;line-height:36px}
.foot-links li:before{content:"»";margin-right:14px}
.field{width:206px;height:46px;border:1px solid #5a6070;border-radius:3px;color:#e6e8ee;font-size:13px;display:flex;align-items:center;padding-left:14px}
.foot-btn{width:206px;height:46px;border-radius:3px;background:var(--red);color:var(--white);font-size:13px;font-weight:700;display:flex;align-items:center;justify-content:center;gap:12px;text-transform:uppercase}
.contact-box{top:4397px;left:202px;width:794px;height:111px;border:1px solid #3a3f4d;display:flex}
.contact-box div{flex:1;display:flex;align-items:center;gap:16px;padding-left:30px;color:var(--white);font-size:16px;line-height:27px;border-right:1px solid #3a3f4d}
.contact-box div:last-child{border-right:none}
.contact-box small{display:block;font-size:12px;font-weight:700;line-height:18px}
.copy{top:4568px;width:1200px;text-align:center;font-size:14px;color:#d7dae2}
</style>
</head>
<body>
<div class="page">

  <!-- header -->
  <header class="abs topbar">
    <div class="abs brand" style="left:110px;top:15px">
      <span class="brand-dot"></span><span class="brand-name">Brightmoor</span>
    </div>
    <div class="abs contact-mini" style="left:372px;top:22px">
      <svg width="30" height="30" viewBox="0 0 30 30" fill="none" stroke="#1b5cb3" stroke-width="2"><rect x="3" y="7" width="24" height="17" rx="2"/><path d="M3 8l12 9 12-9"/></svg>
      <div><small>Send Us Email:</small>info@brightmoorllc.com</div>
    </div>
    <div class="abs contact-mini" style="left:610px;top:22px">
      <svg width="30" height="30" viewBox="0 0 30 30" fill="none" stroke="#1b5cb3" stroke-width="2"><path d="M15 27s-9-9-9-15a9 9 0 0118 0c0 6-9 15-9 15z"/><circle cx="15" cy="12" r="3"/></svg>
      <div><small>Location:</small>4815 Birch Cove Road Wayzata, MN 55391</div>
    </div>
    <div class="abs social" style="left:952px;top:26px"><span></span><span></span><span></span></div>
  </header>

  <nav class="abs navbar">
    <div class="abs nav"><span>Home</span><span>Services</span><span>About Us</span><span>Contact Us</span><span>FAQs</span><span>Employment</span><span>Testimonials</span><span>Gallery</span></div>
    <div class="abs nav-phone"><i><svg width="20" height="20" viewBox="0 0 24 24" fill="none" stroke="#1b5cb3" stroke-width="2"><path d="M5 3h4l2 5-3 2a12 12 0 006 6l2-3 5 2v4a2 2 0 01-2 2A18 18 0 013 5a2 2 0 012-2z"/></svg></i>(952) 555-0148</div>
  </nav>

  <!-- hero -->
  <section class="abs hero" role="img" aria-label="Photo of a wooden dock with a boat lift frame on a calm blue lake">
    <h1 class="abs hero-title">Lake Weed Removal</h1>
    <p class="abs hero-sub">Specializing in Residential commercial</p>
    <div class="abs" style="top:411px;left:515px"><span class="btn">Get Started<i><svg width="14" height="14" viewBox="0 0 14 14"><path d="M4 2l6 5-6 5z" fill="#d21044"/></svg></i></span></div>
    <div class="abs dots"><span></span><span class="on"></span><span></span><span></span></div>
  </section>
  <svg class="abs" style="top:640px;left:0" width="1200" height="220" viewBox="0 0 1200 220">
    <path d="M0 40 C120 190 420 215 700 140 C900 90 1080 50 1200 60 L1200 220 L0 220Z" fill="#d21044"/>
    <path d="M0 75 C140 210 430 225 700 155 C900 105 1080 72 1200 82 L1200 220 L0 220Z" fill="#ffffff"/>
  </svg>

  <!-- services -->
  <div class="abs" style="top:878px;left:14px;width:100px;height:100px;border-radius:50%;background:#eef4fc"></div>
  <h2 class="abs sec-title" style="top:922px">Our Services</h2>
  <div class="abs rule" style="top:973px"></div>
  <p class="abs" style="top:997px;width:1200px;text-align:center;font-size:15px">We know there is no life like the lake life and we are dedicated to keeping it that way.</p>
  <div class="abs dotgrid" style="top:1185px;left:100px;width:40px;height:160px"></div>
  <div class="abs dotgrid" style="top:1080px;left:1050px;width:40px;height:160px"></div>

  <article class="abs card" style="top:1064px;left:120px">
    <div class="abs card-photo" role="img" aria-label="Photo of a person in waders beside a long dock" style="background:linear-gradient(180deg,#b8c3cc,#6f7d87)"></div>
    <div class="abs card-plus">+</div>
    <div class="abs card-body"><div class="card-icon"><span></span></div><div class="card-text"><b>Lake Weed Removal</b>Reclaim open water in front of your dock, beach, or boat slip! Our removal method</div></div>
  </article>
  <article class="abs card" style="top:1064px;left:449px">
    <div class="abs card-photo" role="img" aria-label="Photo of a sandy beach with kayaks and a dock" style="background:linear-gradient(180deg,#5f8a4a,#8a8f6d 60%,#a99b74);border:3px solid #d21044"></div>
    <div class="abs card-plus" style="background:#d21044">+</div>
    <div class="abs card-body"><div class="card-icon" style="background:#fbeef1"><span style="background:#d21044"></span></div><div class="card-text"><b>Zebra Mussel removal</b>This Invasive species is becoming an increasing risk to Minnesota waterways</div></div>
  </article>
  <article class="abs card" style="top:1064px;left:778px">
    <div class="abs card-photo" role="img" aria-label="Photo of divers working among green lake weeds" style="background:linear-gradient(180deg,#5f7a45,#3f5a33)"></div>
    <div class="abs card-plus">+</div>
    <div class="abs card-body"><div class="card-icon"><span></span></div><div class="card-text"><b>Water Trampoline</b>From installation at the start of the season to removal at the end of the season winter</div></div>
  </article>

  <div class="abs arrow-btn" style="top:1209px;left:40px;background:#fff;box-shadow:0 2px 8px rgba(0,0,0,.2)"><svg width="12" height="12" viewBox="0 0 12 12"><path d="M8 2L4 6l4 4" stroke="#222" stroke-width="2" fill="none"/></svg></div>
  <div class="abs arrow-btn" style="top:1209px;left:1120px;background:var(--blue)"><svg width="12" height="12" viewBox="0 0 12 12"><path d="M4 2l4 4-4 4" stroke="#fff" stroke-width="2" fill="none"/></svg></div>

  <!-- about -->
  <section class="abs about">
    <div class="abs" style="top:170px;left:1160px;width:80px;height:80px;border-radius:50%;background:#dde9f7"></div>
    <div class="abs" style="top:590px;left:-50px;width:80px;height:80px;border-radius:50%;background:#dde9f7"></div>
    <div class="abs" style="top:540px;left:850px;width:100px;height:100px;border-radius:50%;background:#e4edf8"></div>
  </section>
  <h2 class="abs sec-title" style="top:1532px">About Us</h2>
  <div class="abs rule" style="top:1583px"></div>
  <p class="abs p-center" style="top:1600px;left:166px;width:868px">Brightmoor LLC is a company formed in response to the increasing incidence of invasive species in Minnesota's lakes and water systems. The impact of these fast-growing nuisances, inspired our venture to effectively control unwanted lake weeds. Brightmoor, LLC helps provide the enjoyable weed-free lake environment craved by water enthusiasts.</p>
  <div class="abs about-photo"><div role="img" aria-label="Photo of a young diver in a wetsuit holding a bundle of pulled lake weeds"></div></div>
  <h3 class="abs sub-title" style="top:1768px;left:575px">Preserving the Good</h3>
  <p class="abs about-text" style="top:1818px;left:575px;width:490px">We have partnered with <b>Greenleaf Compost Co.</b> to recycle 100% of the lake weeds we remove. The types of materials used in compost have a huge impact on how long it takes to break down and how nutrient rich the end product will be. The lake weeds we provide have high levels of moisture as well as critically needed nitrogen. They are a great addition for making high quality compost.</p>
  <div class="abs" style="top:2019px;left:574px"><span class="btn" style="border:3px solid var(--blue);height:44px">Learn More<i><svg width="14" height="14" viewBox="0 0 14 14"><path d="M4 2l6 5-6 5z" fill="#d21044"/></svg></i></span></div>

  <!-- results -->
  <h2 class="abs sec-title" style="top:2251px">Clear Lake Results</h2>
  <div class="abs rule" style="top:2300px"></div>
  <div class="abs dotgrid" style="top:2318px;left:96px;width:170px;height:60px"></div>
  <div class="abs dotgrid" style="top:2480px;left:1000px;width:112px;height:180px"></div>
  <div class="abs result" style="top:2341px;left:111px"><div class="abs result-photo" role="img" aria-label="Photo of a dock covered in pulled weeds, before cleanup" style="background:linear-gradient(180deg,#cfd7de,#6f7e5a 40%,#7a6c58)"></div><div class="abs result-label">Before</div></div>
  <div class="abs result" style="top:2341px;left:359px"><div class="abs result-photo" role="img" aria-label="Photo of the same dock cleared, after cleanup" style="background:linear-gradient(180deg,#d8dfe6,#6b8055 40%,#9c9487)"></div><div class="abs result-label after">After</div></div>
  <div class="abs result" style="top:2341px;left:608px"><div class="abs result-photo" role="img" aria-label="Photo of lake water thick with weeds, before cleanup" style="background:linear-gradient(180deg,#9aa3aa,#7d7a62 60%,#6a5d43)"></div><div class="abs result-label">Before</div></div>
  <div class="abs result" style="top:2341px;left:856px"><div class="abs result-photo" role="img" aria-label="Photo of clear open lake water with a dock lift, after cleanup" style="background:linear-gradient(180deg,#d2d8de,#5b6a78 45%,#3e4d5c)"></div><div class="abs result-label after">After</div></div>

  <!-- testimonials -->
  <section class="abs testi">
    <h2 class="abs testi-title" style="top:108px;left:134px">Our Testimonials</h2>
    <div class="abs" style="top:160px;left:134px;width:52px;height:3px;background:var(--red)"></div>
    <div class="abs" style="top:185px;left:134px;font-family:Georgia,serif;font-size:70px;line-height:60px;color:#fff;font-weight:700">“</div>
    <p class="abs testi-text" style="top:240px;left:152px;width:416px">Everyone used to jump off the water trampoline and instantly get tangled in lake weeds. We contacted Brightmoor and their SCUBA divers have now been solving our problem for the past 4 years!Everyone used to jump off the water trampoline and instantly get tangled in lake weeds. We contacted Brightmoor and their SCUBA divers have now been solving.</p>
    <p class="abs" style="top:396px;left:152px;font-size:15px;font-weight:700;color:#fff">– Hollow Pine Shores Association</p>
    <p class="abs" style="top:436px;left:152px;font-size:15px;color:#fff">Lake Harrowmere</p>
    <div class="abs circle-photo" role="img" aria-label="Photo of a lawn chair and kayaks on a sandy shore" style="top:54px;left:649px;width:232px;height:232px;background:linear-gradient(180deg,#6f8a52,#9b8b68)"></div>
    <div class="abs circle-photo" role="img" aria-label="Photo of a sunset over a lake seen from a dock" style="top:244px;left:850px;width:214px;height:214px;background:linear-gradient(180deg,#5a6f98,#d8905a 55%,#2a2a30)"></div>
    <div class="abs circle-photo" role="img" aria-label="Photo of a boat lift and dock in blue water" style="top:312px;left:645px;width:180px;height:180px;background:linear-gradient(180deg,#9fb3c8,#2f4f7c)"></div>
  </section>

  <!-- faq -->
  <div class="abs" style="top:3870px;left:1030px;width:140px;height:140px;border-radius:50%;background:#eef2f8"></div>
  <h2 class="abs sec-title" style="top:3343px">Frequently Asked Questions</h2>
  <div class="abs rule" style="top:3392px"></div>
  <div class="abs faq-open">
    <p class="abs" style="top:38px;left:30px;font-size:14.5px;font-weight:700;color:var(--ink)">How early do lake weeds start to grow?</p>
    <p class="abs" style="top:70px;left:30px;width:620px;font-size:14.5px;line-height:25px">Curly-leaf pondweed is one of the first plants to grow in early spring (and typically dies off the quickest at the end of the summer). This is heavily dependent on sunlight, how fast the water warms up, and sediment type (sand versus muck).</p>
    <div class="abs" style="top:32px;left:773px;width:34px;height:34px;border-radius:50%;background:var(--blue)"><div class="abs" style="top:15px;left:10px;width:14px;height:3px;background:#fff"></div></div>
  </div>
  <div class="abs faq-item" style="top:3621px">How fast do lake weeds grow?<i>+</i></div>
  <div class="abs faq-item" style="top:3694px">What if the treatment area encroaches your neighbor’s shoreline?<i>+</i></div>
  <div class="abs faq-item" style="top:3766px">What if the treatment area encroaches your neighbor’s shoreline?<i>+</i></div>
  <div class="abs faq-item" style="top:3838px">How big of an area can I treat?<i>+</i></div>

  <!-- footer -->
  <svg class="abs" style="top:3960px;left:0" width="1200" height="100" viewBox="0 0 1200 100">
    <path d="M0 100 L0 85 C300 20 700 15 1200 40 L1200 100Z" fill="#0b0e1a"/>
    <path d="M0 85 C300 22 700 15 1200 32 L1200 44 C700 28 300 34 0 95Z" fill="#d21044"/>
  </svg>
  <footer class="abs footer">
    <div class="abs brand" style="left:110px;top:82px"><span class="brand-dot"></span><span class="brand-name">Brightmoor</span></div>
    <p class="abs" style="top:150px;left:110px;width:260px;font-size:14.5px;line-height:24px;color:#e6e8ee">Brightmoor LLC is a company formed in response to increasing incidence of invasive species in Minnesota's lakes and water systems.</p>
    <div class="abs" style="top:252px;left:110px;display:flex;gap:10px">
      <span style="width:34px;height:34px;border-radius:50%;border:1px solid #e6e8ee"></span><span style="width:34px;height:34px;border-radius:50%;border:1px solid #e6e8ee"></span><span style="width:34px;height:34px;border-radius:50%;border:1px solid #e6e8ee"></span><span style="width:34px;height:34px;border-radius:50%;border:1px solid #e6e8ee"></span>
    </div>
    <div class="abs" style="top:68px;left:447px"><h4 class="foot-head">Other Links</h4><ul class="foot-links" style="margin-top:12px"><li>Team</li><li>FAQ</li><li>Terms Of Use</li><li>Privacy Policy</li><li>Contact Us</li></ul></div>
    <div class="abs" style="top:68px;left:678px"><h4 class="foot-head">Useful Links</h4><ul class="foot-links" style="margin-top:12px"><li>Home</li><li>Services</li><li>About Us</li><li>Testimonials</li><li>More</li></ul></div>
    <div class="abs" style="top:68px;left:883px"><h4 class="foot-head">Get In Touch</h4>
      <div class="field" style="margin-top:22px">Name:</div>
      <div class="field" style="margin-top:14px">Email:</div>
      <div class="foot-btn" style="margin-top:14px">Submit Now<svg width="16" height="16" viewBox="0 0 16 16"><circle cx="8" cy="8" r="7" fill="#fff"/><path d="M6 4l5 4-5 4z" fill="#d21044"/></svg></div>
    </div>
  </footer>
  <div class="abs contact-box">
    <div><svg width="30" height="30" viewBox="0 0 30 30" fill="none" stroke="#fff" stroke-width="2"><rect x="3" y="7" width="24" height="17" rx="2"/><path d="M3 8l12 9 12-9"/></svg><span><small>Send Us Email:</small>info@brightmoorllc.com</span></div>
    <div><svg width="30" height="30" viewBox="0 0 24 24" fill="none" stroke="#fff" stroke-width="1.8"><path d="M5 3h4l2 5-3 2a12 12 0 006 6l2-3 5 2v4a2 2 0 01-2 2A18 18 0 013 5a2 2 0 012-2z"/></svg><span><small>Contact Now:</small>(952) 555-0148</span></div>
    <div style="padding-left:22px"><svg width="30" height="30" viewBox="0 0 30 30" fill="none" stroke="#fff" stroke-width="2"><path d="M15 27s-9-9-9-15a9 9 0 0118 0c0 6-9 15-9 15z"/><circle cx="15" cy="12" r="3"/></svg><span><small>Location:</small>4815 Birch Cove Road Wayzata, MN 55391</span></div>
  </div>
  <p class="abs copy">©Copyrights 2022 Brightmoor All Rights Reserved.</p>

</div>
</body>
</html>
```